2 banners on the outside wall of the hall

Banner 1:
KalviMar specializes in the planning, construction, and maintenance of high-quality pond systems, particularly swimming ponds, natural pools, garden ponds, koi ponds, streams, and waterfalls. Learn more at www.kalvimar.de
The following data should be included:
Planning and construction of swimming ponds and natural pools, as well as garden ponds and koi ponds
100% organic
Individually planned
Over 20 years of experience
04627 3150962
www.kalvimar.de
“Logo-KalviMar”
Banner 2:
Grünflut-Laden is the online shop for high-quality aquatic plants for ponds and aquariums.
More information at https://gruenflut-laden.de
Online shop for pond plants and water lilies, as well as aquarium plants and accessories
Over 400 plant species
Top gardener quality
Secure packaging & fast shipping
04627 3150961
www.gruenflut-laden. de
“Logo Greenflow shop”
Here's roughly what we envision:
The designs for each banner should be clearly visible and include everything needed, without appearing cluttered. In other words, it should be immediately clear what the banner is about.
We should also be made aware of our unique selling points and advantages.
It is important that the banners also harmonize visually with each other.
We liked the banner image in the attachment and it serves as inspiration.
The banner print data is produced as follows:
• Banner size: Width x Height: 3880 mm x 1880 mm
• Material: Mesh banner, PVFormat: PDF (X-3:2000)
• Fonts: converted into paths
• Trim allowance: +2 mm all around
• Color space: CMYK
• Resolution: 72 dpi (recommended) at 1:1 resolution
Look and feel
Each slider illustrates characteristics of the customer's brand and the style your logo design should communicate.

```html
<!DOCTYPE html>
<html lang="de">
<head>
<meta charset="utf-8">
<title>KalviMar – Banner</title>
<link rel="stylesheet" href="https://fonts.googleapis.com/css2?family=Barlow:wght@400;600;700&family=Barlow+Semi+Condensed:wght@400&display=swap">
<style>
  :root {
    --brand-blue: #2b5d87;
    --wave-mid: #6a93b6;
    --wave-light: #9db3cb;
    --frame: #1b1b1b;
    --white: #ffffff;
  }
  * { margin: 0; padding: 0; box-sizing: border-box; }
  html, body {
    width: 1200px; height: 667px; overflow: hidden; background: var(--white);
  }
  .canvas {
    position: relative; width: 1200px; height: 667px;
    font-family: "Barlow", Arial, sans-serif; color: var(--brand-blue);
  }
  .size-label {
    position: absolute; left: 938px; top: 14px;
    font-size: 20px; font-weight: 400; color: var(--brand-blue);
  }
  .shapes { position: absolute; inset: 0; }
  .headline {
    position: absolute; left: 75px; width: 1062px; top: 96px;
    text-align: center; color: var(--white);
    font-size: 38px; line-height: 41px; letter-spacing: 1.4px; font-weight: 400;
  }
  .photo { position: absolute; }
  .photo--pool {
    left: 157px; top: 268px; width: 257px; height: 160px;
    clip-path: polygon(0 0, 100% 0, 100% 100%, 11% 100%, 0 86%);
    background: linear-gradient(90deg, #2fb9c4 0%, #44c6cf 45%, #9a9790 55%, #b3afa8 100%);
  }
  .photo--swimpond {
    left: 427px; top: 240px; width: 355px; height: 217px;
    clip-path: polygon(0 0, 95% 0, 100% 7%, 100% 100%, 5% 100%, 0 92%);
    background: linear-gradient(180deg, #a4553f 0%, #7f8f4c 22%, #4f86a6 45%, #6aa0bf 62%, #a39a7e 82%, #8e8a7a 100%);
  }
  .photo--naturalpool {
    left: 795px; top: 268px; width: 256px; height: 159px;
    clip-path: polygon(0 0, 94% 0, 100% 9%, 100% 100%, 0 100%);
    background: linear-gradient(180deg, #4e6f3a 0%, #6d8b45 28%, #5c8b62 50%, #4f7d69 75%, #3f6a5d 100%);
  }
  .usp {
    position: absolute; display: flex; align-items: center; gap: 13px;
    font-family: "Barlow Semi Condensed", "Barlow", sans-serif;
    font-size: 28px; font-weight: 400; letter-spacing: 0.3px; color: var(--brand-blue);
    white-space: nowrap; line-height: 1;
  }
  .usp::before {
    content: ""; width: 13px; height: 13px; background: var(--brand-blue); flex: none;
  }
  .usp--organic { left: 177px; top: 437px; }
  .usp--experience { left: 449px; top: 469px; }
  .usp--planned { left: 803px; top: 434px; }
  .brand-name {
    position: absolute; left: 157px; top: 492px;
    font-size: 54px; font-weight: 700; color: var(--brand-blue); letter-spacing: -0.5px;
  }
  .website {
    position: absolute; left: 427px; width: 355px; top: 538px;
    text-align: center; color: var(--white); font-size: 31px; font-weight: 400;
  }
  .phone-icon { position: absolute; left: 1025px; top: 487px; width: 29px; height: 24px; }
  .phone-number {
    position: absolute; left: 795px; top: 513px;
    font-size: 39px; font-weight: 700; letter-spacing: 0.2px; color: var(--brand-blue);
  }
</style>
</head>
<body>
<div class="canvas">
  <div class="size-label">3880mm x 1880mm</div>

  <svg class="shapes" width="1200" height="667" viewBox="0 0 1200 667" aria-hidden="true">
    <path class="header-wave-light" fill="var(--wave-light)"
      d="M75,64 H1137 V171 L952,235 Q905,212 770,212 Q420,216 75,204 Z"/>
    <path class="header-wave-mid" fill="var(--wave-mid)"
      d="M75,64 H1137 V171 L1052,200 Q990,186 830,192 Q460,210 75,203 Z"/>
    <path class="header-band" fill="var(--brand-blue)"
      d="M75,64 H1137 V171 L1052,200 Q960,181 720,195 Q360,213 75,202 Z"/>
    <path class="footer-band" fill="var(--brand-blue)"
      d="M59,570 H427 L462,536 H748 L781,570 H1131 V600 H59 Z"/>
    <rect class="frame" x="83" y="83" width="1041" height="504" fill="none" stroke="var(--frame)" stroke-width="1"/>
  </svg>

  <h1 class="headline">Planung und Bau von Schwimmteichen und<br>Naturpools sowie Gartenteichen und Koiteichen</h1>

  <div class="photo photo--pool" role="img" aria-label="Foto: Naturpool mit Holzdeck und Liegen"></div>
  <div class="photo photo--swimpond" role="img" aria-label="Foto: Schwimmteich mit Kieselufer vor einem Backsteinhaus"></div>
  <div class="photo photo--naturalpool" role="img" aria-label="Foto: Naturteich mit Seerosen und Holzplattform"></div>

  <p class="usp usp--organic">100% biologisch</p>
  <p class="usp usp--experience">Über 20 Jahre Erfahrung</p>
  <p class="usp usp--planned">Individuell geplant</p>

  <div class="brand-name">KalviMar</div>

  <div class="website">www.kalvimar.de</div>

  <svg class="phone-icon" viewBox="0 0 29 24" aria-hidden="true">
    <path fill="var(--brand-blue)" d="M2,8 Q2,1 14.5,1 Q27,1 27,8 L27,10 L21,10 L20,6 L9,6 L8,10 L2,10 Z"/>
    <path fill="var(--brand-blue)" d="M6,10 L9,7 H20 L23,10 L26,22 Q26,24 24,24 H5 Q3,24 3,22 Z"/>
    <g fill="var(--white)">
      <rect x="11" y="12" width="2" height="2"/><rect x="14" y="12" width="2" height="2"/><rect x="17" y="12" width="2" height="2"/>
      <rect x="11" y="15" width="2" height="2"/><rect x="14" y="15" width="2" height="2"/><rect x="17" y="15" width="2" height="2"/>
      <rect x="11" y="18" width="2" height="2"/><rect x="14" y="18" width="2" height="2"/><rect x="17" y="18" width="2" height="2"/>
    </g>
  </svg>
  <div class="phone-number">04627 3150962</div>
</div>
</body>
</html>
```